Probate (Legal) Wordpress Design with Coding for Online Company

I need a Wordpress design with coding, pictures, content to be provided by me, fully responsive, and development. This is for a 6-7 page design.

Pages Needed: Home/About/Probate/Process/FAQ/Contact Us/Blog.

The home page should be organized as followed:
-Steps in Probate: Gather; Implement; Close (each step will come with content)
-Flat-Fee Price & Savings: Content will go here with a button to contact us (phone number) or just the phone number.
-You Have Questions, We Have Answers: five questions with content. Only one question answer to show at a time when clicked on the question from the list.
-Get to Know Us: a brief description with content about what we do and who we are.

Main image slogan: Helping Californians deal with loss with DIGNITY & UNDERSTATING (you may use a better slogan if you wish).

The Contact page should not have a map since we are an online company. We service the entire state of California in every county and city.

The About page should be simple, direct, and easy on the eye. It should have a brief description of who we are and it should have no more than 6 reasons why the client should hire us.

About our online California company. We are not attorneys but legal document assistants who prepare legal documents for probate estate when someone dies with or without a will and assets need to be distributed. We have a flat-fee for Formal Probate of $999 and $699 for Informal Probate. We are an online company and offer our services to the entire state of California in every county. We do everything over the phone and email. The turn around time for us to prepare the initial legal paperwork for the client is within 3-5 business days. We can prepare, file, serve and manage a probate matter from petition to closing. We are not attorneys so our prices are very affordable compare to the attorney.

The company name for the website will be www.velmarhollow.com, The Velmar Hollow Group.

I do not have a logo yet. The colors of the website should be easy on the eye and calming. THE SITE SHOULD BE SIMPLE AND STRAIGHT TO THE POINT. EASY TO NAVIGATE.

The company phone number should be very visible and should stand out to the client. It should also be clickable and ready to dial for smartphone users.

I do not want a contact form on the homepage. THE MAIN THING IS FOR THE POTENTIAL CLIENT TO CALL OUR OFFICE TO SIGN UP.

I do like some images of family or people since we are dealing with people who just lost a loved one. Not all the images have to be of people.

The site should not look like we practice law or that people can mistake us for attorneys.

Target Market(s)

People who just lost a loved one who had property, assets, in California but died with or without a will or trust. This is for people looking to hire non-attorneys.

Coding

Coded - Design and coding required

Font styles to use
Serif

Colors

Designer to choose colors to be used in the design.

Requirements
Must have
• Refer to Project Description.
Nice to have
• The sample images provided is what I am attracted to for the homepage image.
Should not have

```html
<!DOCTYPE html>
<html lang="en">
<head>
<meta charset="utf-8">
<title>The Velmar Hollow Group — Probate Document Assistance</title>
<link href="https://fonts.googleapis.com/css2?family=Nunito+Sans:wght@400;600;700&family=Open+Sans:wght@400;600;700&display=swap" rel="stylesheet">
<style>
:root{
  --blue:#0a6dbb;
  --blue-dark:#085d9f;
  --ink:#2f3235;
  --text:#3b3e42;
  --muted:#9a9a9a;
  --panel:#ececec;
  --panel-line:#dcdcdc;
  --strip:#676767;
  --footer:#333333;
  --white:#ffffff;
}
*{margin:0;padding:0;box-sizing:border-box}
html,body{width:1200px;height:2459px;overflow:hidden;background:var(--white)}
body{position:relative;font-family:"Open Sans",sans-serif;color:var(--text)}
.heading{font-family:"Nunito Sans",sans-serif}
.wrap{position:absolute;left:133px;width:934px}

/* header */
.site-header{position:absolute;top:0;left:0;width:1200px;height:102px}
.brand{position:absolute;left:133px;top:24px;font-family:"Nunito Sans",sans-serif;font-weight:700;font-size:38px;color:var(--blue);line-height:1.2}
.header-phone{position:absolute;right:133px;top:38px;font-size:19px;color:var(--ink);display:flex;align-items:center;gap:9px}
.main-nav{position:absolute;top:102px;left:0;width:1200px;height:41px;background:var(--blue)}
.main-nav ul{list-style:none;position:absolute;left:133px;width:934px;height:41px;display:flex}
.main-nav li{height:41px;line-height:41px;text-align:center;color:var(--white);font-size:13px;font-weight:600;letter-spacing:.3px}
.main-nav li.active{background:var(--footer)}

/* hero */
.hero{position:absolute;top:143px;left:0;width:1200px;height:472px;
  background:linear-gradient(180deg,#7fa6c9 0%,#aac5dc 35%,#d7e3ec 70%,#eef1f2 100%)}
.hero-figure{position:absolute;left:560px;top:0;width:420px;height:472px;
  background:radial-gradient(ellipse at 50% 60%,rgba(214,200,180,.8) 0%,rgba(200,190,175,.4) 45%,rgba(200,190,175,0) 70%)}
.hero-text{position:absolute;left:133px;top:203px}
.hero-text .lead{font-family:"Nunito Sans",sans-serif;font-size:21px;color:var(--ink)}
.hero-text h1{font-family:"Nunito Sans",sans-serif;font-size:31px;font-weight:700;color:var(--ink);letter-spacing:.5px;margin-top:2px}
.hero-arrow{position:absolute;top:219px}

/* intro tabs */
.intro-tabs{top:675px;left:375px;width:448px;height:53px}
.tab{position:absolute;top:0;height:53px;line-height:50px;text-align:center;font-family:"Nunito Sans",sans-serif;font-size:24px;font-weight:600}
.tab-active{left:0;width:218px;background:var(--blue);color:var(--white)}
.tab-active::after{content:"";position:absolute;left:99px;bottom:-10px;border-left:10px solid transparent;border-right:10px solid transparent;border-top:10px solid var(--blue)}
.tab-idle{left:228px;width:220px;background:#f0f0f0;color:var(--muted);border-bottom:4px solid var(--blue)}
.intro-text{top:752px;font-size:11.6px;line-height:20.5px;text-align:center;color:var(--text)}

/* steps */
.steps{position:absolute;top:893px;left:0;width:1200px;height:391px;background:var(--blue);color:var(--white)}
.steps h2{position:absolute;top:56px;width:1200px;text-align:center;font-size:32px;font-weight:600}
.step{position:absolute;top:131px;width:300px;text-align:center}
.step svg{display:block;margin:0 auto}
.step h3{font-family:"Nunito Sans",sans-serif;font-weight:400;font-size:24px;margin-top:11px}
.step p{font-size:10.2px;line-height:17px;margin-top:4px;color:#dfeaf5}

/* flat fee */
.flat-fee{position:absolute;top:1285px;left:0;width:1200px;height:341px;
  background:linear-gradient(90deg,#cfcfcf 0%,#dadada 40%,#eceeef 62%,#f4f5f6 100%)}
.flat-fee-photo{position:absolute;left:620px;top:0;width:580px;height:341px;
  background:radial-gradient(ellipse at 62% 62%,rgba(214,170,160,.55) 0%,rgba(230,225,225,.35) 30%,rgba(240,242,244,0) 60%)}
.flat-fee h2{position:absolute;left:130px;top:71px;font-size:32px;font-weight:600;color:var(--blue)}
.flat-fee p{position:absolute;left:133px;top:122px;width:560px;font-size:15px;line-height:23px;color:var(--ink);white-space:nowrap}
.btn{position:absolute;top:207px;height:43px;background:var(--blue);color:var(--white);display:flex;align-items:center;justify-content:center;gap:9px}
.btn-contact{left:133px;width:141px;font-size:14px;font-weight:700;letter-spacing:.4px}
.btn-phone{left:285px;width:180px;font-size:19px}

/* faq */
.faq h2{position:absolute;top:1695px;left:0;width:1200px;text-align:center;font-size:32px;font-weight:600;color:var(--blue)}
.faq-item{position:absolute;left:133px;width:934px;height:46px;background:var(--panel);display:flex;align-items:center;padding:0 16px;font-size:18.5px;color:var(--ink)}
.faq-item .q{margin-left:14px;flex:1}
.faq-answer{position:absolute;left:133px;top:1815px;width:934px;height:132px;background:#f4f4f4;border:1px solid var(--panel);padding:20px 48px 0 48px;font-size:11.6px;line-height:19.5px;color:#555}

/* contact strip & footer */
.contact-strip{position:absolute;top:2250px;left:0;width:1200px;height:79px;background:var(--strip);color:var(--white);font-size:18px}
.contact-strip .item{position:absolute;top:27px;display:flex;align-items:center;gap:10px}
.site-footer{position:absolute;top:2329px;left:0;width:1200px;height:130px;background:var(--footer);color:#cfcfcf}
.footer-links{position:absolute;left:133px;top:40px;font-size:11px}
.footer-links span.sep{margin:0 8px}
.copyright{position:absolute;left:133px;top:71px;font-size:11px}
.social{position:absolute;top:52px;width:24px;height:24px;border-radius:50%}
</style>
</head>
<body>

<header class="site-header">
  <div class="brand">The Velmar Hollow Group</div>
  <div class="header-phone">
    <svg width="16" height="16" viewBox="0 0 24 24"><path d="M6.6 10.8a15.1 15.1 0 0 0 6.6 6.6l2.2-2.2c.3-.3.7-.4 1-.2 1.1.4 2.3.6 3.6.6.6 0 1 .4 1 1V20c0 .6-.4 1-1 1A17 17 0 0 1 3 4c0-.6.4-1 1-1h3.5c.6 0 1 .4 1 1 0 1.3.2 2.5.6 3.6.1.3 0 .7-.2 1z" fill="#2f3235"/></svg>
    555 014 2287
  </div>
</header>

<nav class="main-nav">
  <ul>
    <li class="active" style="width:118px">HOME</li>
    <li style="width:118px">ABOUT</li>
    <li style="width:135px">PROBATE</li>
    <li style="width:149px">PROCESS</li>
    <li style="width:108px">FAQ</li>
    <li style="width:156px">CONTACT US</li>
    <li style="width:150px">BLOG</li>
  </ul>
</nav>

<section class="hero">
  <div class="hero-figure" role="img" aria-label="Photo of a family seen from behind, embracing under a bright sky"></div>
  <svg class="hero-arrow" style="left:46px" width="20" height="30" viewBox="0 0 20 30"><path d="M15 3 4 15l11 12" fill="none" stroke="#fff" stroke-width="4"/></svg>
  <svg class="hero-arrow" style="left:1134px" width="20" height="30" viewBox="0 0 20 30"><path d="M5 3l11 12L5 27" fill="none" stroke="#fff" stroke-width="4"/></svg>
  <div class="hero-text">
    <p class="lead">Helping Californians deal with loss with</p>
    <h1>DIGNITY &amp; UNDERSTATING</h1>
  </div>
</section>

<section class="intro">
  <div class="wrap intro-tabs">
    <div class="tab tab-active">WHO WE ARE</div>
    <div class="tab tab-idle">WHAT WE DO</div>
  </div>
  <p class="wrap intro-text">We are not attorneys but legal document assistants who prepare legal documents for probate estate when someone dies with or without a will and assets need to be distributed. We have a flat-fee for Formal Probate of $999 and $699 for Informal Probate. We are an online company and offer our services to the entire state of California in every county. We do everything over the phone and email. The turn around time for us to prepare the initial legal paperwork for the client is within 3-5 business days. We can prepare, file, serve and manage a probate matter from petition to closing. We are not attorneys so our prices are very affordable compare to the attorney.</p>
</section>

<section class="steps">
  <h2 class="heading">Steps in Probate</h2>
  <div class="step" style="left:129px">
    <svg width="84" height="84" viewBox="0 0 84 84"><circle cx="42" cy="42" r="40" fill="none" stroke="#fff" stroke-width="2"/><path d="M30 32h14M30 32v24h24V42" fill="none" stroke="#fff" stroke-width="2.2"/><path d="M38 46l2-6 13-13 4 4-13 13z" fill="none" stroke="#fff" stroke-width="2.2"/></svg>
    <h3>Gather</h3>
    <p>Proin placerat dapibus gravida. In tristique tristique nulla eget hendrerit. Maecenas vel tortor accumsan quam varius imperdiet vel eget facilisis tincidunt lectus.</p>
  </div>
  <div class="step" style="left:451px">
    <svg width="84" height="84" viewBox="0 0 84 84"><circle cx="42" cy="42" r="40" fill="none" stroke="#fff" stroke-width="2"/><circle cx="42" cy="42" r="13" fill="none" stroke="#fff" stroke-width="5" stroke-dasharray="5 5.2"/><circle cx="42" cy="42" r="10" fill="none" stroke="#fff" stroke-width="2.2"/><circle cx="42" cy="42" r="4.5" fill="none" stroke="#fff" stroke-width="2"/></svg>
    <h3>Implement</h3>
    <p>Proin placerat dapibus gravida. In tristique tristique nulla eget hendrerit. Maecenas vel tortor accumsan quam varius imperdiet vel eget facilisis tincidunt lectus.</p>
  </div>
  <div class="step" style="left:773px">
    <svg width="84" height="84" viewBox="0 0 84 84"><circle cx="42" cy="42" r="40" fill="none" stroke="#fff" stroke-width="2"/><path d="M31 26h16l7 7v23H31z" fill="none" stroke="#fff" stroke-width="2.2"/><path d="M35 36h12M35 41h12M35 46h7" stroke="#fff" stroke-width="2"/><circle cx="52" cy="53" r="6" fill="var(--blue)" stroke="#fff" stroke-width="2"/><path d="M49 53l2 2 4-4" fill="none" stroke="#fff" stroke-width="1.8"/></svg>
    <h3>Close</h3>
    <p>Proin placerat dapibus gravida. In tristique tristique nulla eget hendrerit. Maecenas vel tortor accumsan quam varius imperdiet vel eget facilisis tincidunt lectus.</p>
  </div>
</section>

<section class="flat-fee">
  <div class="flat-fee-photo" role="img" aria-label="Photo of a hand signing a document with a fountain pen"></div>
  <h2 class="heading">Flat-Fee Price &amp; Savings</h2>
  <p>Etiam mattis augue vehicula odio posuere, sit amet tempus lectus<br>luctus. Nulla facilisi. Etiam vel massa elementum, bibendum tellus<br>venenatis, feugiat massa. Curabitur venenatis lacinia ornare.</p>
  <div class="btn btn-contact">CONTACT US</div>
  <div class="btn btn-phone">
    <svg width="15" height="15" viewBox="0 0 24 24"><path d="M6.6 10.8a15.1 15.1 0 0 0 6.6 6.6l2.2-2.2c.3-.3.7-.4 1-.2 1.1.4 2.3.6 3.6.6.6 0 1 .4 1 1V20c0 .6-.4 1-1 1A17 17 0 0 1 3 4c0-.6.4-1 1-1h3.5c.6 0 1 .4 1 1 0 1.3.2 2.5.6 3.6.1.3 0 .7-.2 1z" fill="#fff"/></svg>
    555 014 2287
  </div>
</section>

<section class="faq">
  <h2 class="heading">You Have Questions? We Have Answers...</h2>
  <div class="faq-item" style="top:1770px">
    <svg width="18" height="18" viewBox="0 0 18 18"><circle cx="9" cy="9" r="9" fill="#2f3235"/><path d="M6.5 7a2.5 2.5 0 1 1 3.3 2.3c-.5.2-.8.6-.8 1.1v.6" fill="none" stroke="#fff" stroke-width="1.8"/><circle cx="9" cy="13.6" r="1.1" fill="#fff"/></svg>
    <span class="q">Pellentesque convallis molestie enim sit amet efficitur?</span>
    <svg width="14" height="9" viewBox="0 0 14 9"><path d="M1 1l6 6 6-6" fill="none" stroke="#2f3235" stroke-width="1.8"/></svg>
  </div>
  <div class="faq-answer">Etiam id imperdiet lectus. Vivamus lacus justo, ultrices nec erat in, euismod iaculis mauris. Vivamus eleifend vitae nulla vel malesuada. In ac malesuada lacus, et consectetur ante. Fusce vitae lectus sit amet mi pulvinar maximus. Aenean placerat, nibh vel accumsan aliquet, magna nibh accumsan nibh, ac tempus nunc ipsum ac tellus. Cras augue magna, placerat eget nulla non, congue suscipit neque. Proin a dolor mauris. Vestibulum ante ipsum primis in faucibus orci luctus et ultrices posuere cubilia Curae; Vestibulum eget nisl metus. Phasellus nisl est, condimentum vitae faucibus.</div>
  <div class="faq-item" style="top:1954px">
    <svg width="18" height="18" viewBox="0 0 18 18"><circle cx="9" cy="9" r="9" fill="#2f3235"/><path d="M6.5 7a2.5 2.5 0 1 1 3.3 2.3c-.5.2-.8.6-.8 1.1v.6" fill="none" stroke="#fff" stroke-width="1.8"/><circle cx="9" cy="13.6" r="1.1" fill="#fff"/></svg>
    <span class="q">Nunc sit amet consequat risus?</span>
    <svg width="14" height="9" viewBox="0 0 14 9"><path d="M1 1l6 6 6-6" fill="none" stroke="#2f3235" stroke-width="1.8"/></svg>
  </div>
  <div class="faq-item" style="top:2010px">
    <svg width="18" height="18" viewBox="0 0 18 18"><circle cx="9" cy="9" r="9" fill="#2f3235"/><path d="M6.5 7a2.5 2.5 0 1 1 3.3 2.3c-.5.2-.8.6-.8 1.1v.6" fill="none" stroke="#fff" stroke-width="1.8"/><circle cx="9" cy="13.6" r="1.1" fill="#fff"/></svg>
    <span class="q">Curabitur ac elit leo in eleifend dui tellus in scelerisque elit porttitor?</span>
    <svg width="14" height="9" viewBox="0 0 14 9"><path d="M1 1l6 6 6-6" fill="none" stroke="#2f3235" stroke-width="1.8"/></svg>
  </div>
  <div class="faq-item" style="top:2065px">
    <svg width="18" height="18" viewBox="0 0 18 18"><circle cx="9" cy="9" r="9" fill="#2f3235"/><path d="M6.5 7a2.5 2.5 0 1 1 3.3 2.3c-.5.2-.8.6-.8 1.1v.6" fill="none" stroke="#fff" stroke-width="1.8"/><circle cx="9" cy="13.6" r="1.1" fill="#fff"/></svg>
    <span class="q">Integer eu massa lacinia lacinia nulla non volutpat purus?</span>
    <svg width="14" height="9" viewBox="0 0 14 9"><path d="M1 1l6 6 6-6" fill="none" stroke="#2f3235" stroke-width="1.8"/></svg>
  </div>
  <div class="faq-item" style="top:2121px">
    <svg width="18" height="18" viewBox="0 0 18 18"><circle cx="9" cy="9" r="9" fill="#2f3235"/><path d="M6.5 7a2.5 2.5 0 1 1 3.3 2.3c-.5.2-.8.6-.8 1.1v.6" fill="none" stroke="#fff" stroke-width="1.8"/><circle cx="9" cy="13.6" r="1.1" fill="#fff"/></svg>
    <span class="q">Aenean sed quam non sapien faucibus consequat vitae?</span>
    <svg width="14" height="9" viewBox="0 0 14 9"><path d="M1 1l6 6 6-6" fill="none" stroke="#2f3235" stroke-width="1.8"/></svg>
  </div>
</section>

<section class="contact-strip">
  <div class="item" style="left:133px">
    <svg width="13" height="18" viewBox="0 0 13 18"><path d="M6.5 0A6.5 6.5 0 0 0 0 6.5C0 11 6.5 18 6.5 18S13 11 13 6.5A6.5 6.5 0 0 0 6.5 0z" fill="#fff"/><circle cx="6.5" cy="6.5" r="2.4" fill="#676767"/></svg>
    24 Building name, Street name, City - Zipcode
  </div>
  <div class="item" style="left:605px">
    <svg width="16" height="16" viewBox="0 0 24 24"><path d="M6.6 10.8a15.1 15.1 0 0 0 6.6 6.6l2.2-2.2c.3-.3.7-.4 1-.2 1.1.4 2.3.6 3.6.6.6 0 1 .4 1 1V20c0 .6-.4 1-1 1A17 17 0 0 1 3 4c0-.6.4-1 1-1h3.5c.6 0 1 .4 1 1 0 1.3.2 2.5.6 3.6.1.3 0 .7-.2 1z" fill="#fff"/></svg>
    555 014 2290
  </div>
  <div class="item" style="right:133px">
    <svg width="18" height="14" viewBox="0 0 18 14"><rect width="18" height="14" rx="1.5" fill="#fff"/><path d="M1 1.5l8 6 8-6" fill="none" stroke="#676767" stroke-width="1.6"/></svg>
    info@velmarhollow.com
  </div>
</section>

<footer class="site-footer">
  <div class="footer-links">Home<span class="sep">|</span>About<span class="sep">|</span>Probate<span class="sep">|</span>Process<span class="sep">|</span>FAQ<span class="sep">|</span>Contact Us<span class="sep">|</span>Blog</div>
  <div class="copyright">Copyright &copy; 2017 &nbsp; The Velmar Hollow Group. &nbsp; All rights reserved.</div>
  <span class="social" style="left:975px;background:#3b5a9a"></span>
  <span class="social" style="left:1008px;background:#2aa3dc"></span>
  <span class="social" style="left:1040px;background:#1a79b5"></span>
</footer>

</body>
</html>
```